business card

Business card for new business.
Red and black corporate colors.
Card can have an Indsutrial feel to it. Feel free to add Rust, Bolted steel, or graphics as you see fit. We provide highly specialized services to the below mentioned industries.
Keep information out of corners so that if I want I can choose rounded corners.
Information
- front. name - title - phone - email
- Rear
Pipelines - Marine - Fabrication - Forestry - Power
Ridgeford - Ashbury - Port Caldwell - Elmstone - Harrowgate

```html
<!DOCTYPE html>
<html lang="en">
<head>
<meta charset="utf-8">
<title>Ironspan Business Card</title>
<link href="https://fonts.googleapis.com/css2?family=PT+Sans:wght@400;700&display=swap" rel="stylesheet">
<style>
  :root {
    --backdrop: #1f1f1f;
    --paper: #f3f3f3;
    --brand-red: #dd0010;
    --ink-grey: #777777;
    --ink-dark: #4a4a4a;
    --divider: #c8c8c8;
    --white: #ffffff;
  }
  * { margin: 0; padding: 0; box-sizing: border-box; }
  html, body {
    width: 1200px; height: 960px; overflow: hidden;
    background: var(--backdrop);
    font-family: "PT Sans", Arial, sans-serif;
  }
  .card {
    position: absolute;
    width: 600px; height: 342px;
  }
  .card-front {
    left: 302px; top: 124px;
    background: var(--paper);
    border-bottom: 10px solid var(--brand-red);
  }
  .card-back {
    left: 299px; top: 493px;
    background: var(--brand-red);
  }
  .wordmark {
    position: absolute; left: 0; right: 0;
    text-align: center;
    font-weight: 700;
    font-size: 60px;
    letter-spacing: 1px;
    line-height: 1;
  }
  .card-front .wordmark { top: 93px; color: var(--ink-grey); }
  .card-back .wordmark { top: 132px; color: var(--white); }

  .person {
    position: absolute; right: 337px; top: 217px;
    text-align: right;
  }
  .person-name {
    color: var(--brand-red);
    font-weight: 700; font-size: 21px; line-height: 1.15;
  }
  .person-title {
    color: var(--ink-grey);
    font-size: 15px; text-transform: uppercase; line-height: 1.3;
  }
  .divider {
    position: absolute; left: 291px; top: 204px;
    width: 1px; height: 70px; background: var(--divider);
  }
  .contact {
    position: absolute; left: 319px; top: 210px;
    list-style: none;
  }
  .contact li {
    display: flex; align-items: center;
    height: 19px;
    font-size: 15px; color: var(--ink-dark);
  }
  .contact svg { width: 13px; height: 13px; margin-right: 8px; fill: var(--brand-red); }

  .services {
    position: absolute; left: 0; right: 0; top: 255px;
    text-align: center; color: var(--white);
    font-size: 15.5px; line-height: 19.5px;
  }
  .services .dot { font-size: 11px; margin-right: 2px; vertical-align: 1px; }
</style>
</head>
<body>

<section class="card card-front">
  <div class="wordmark">IRONSPAN</div>

  <div class="person">
    <div class="person-name">MARCUS HALE</div>
    <div class="person-title">President</div>
  </div>

  <div class="divider"></div>

  <ul class="contact">
    <li>
      <svg viewBox="0 0 16 16" aria-hidden="true"><path d="M2 5c0-2 2-3 6-3s6 1 6 3v1h-3V4.5c-1-.4-5-.4-6 0V6H2zM4 7h8l2 6H2z M8 8.5a2 2 0 1 0 0 4 2 2 0 0 0 0-4z"/></svg>
      555 0142 7781
    </li>
    <li>
      <svg viewBox="0 0 16 16" aria-hidden="true"><path d="M1 4h14v1L8 9 1 5z M1 6.5l7 4 7-4V12H1z"/></svg>
      marcus@ironspan.com
    </li>
    <li>
      <svg viewBox="0 0 16 16" aria-hidden="true"><circle cx="8" cy="8" r="7"/><path d="M5 4c2 0 3 1 2 3s1 2 0 4M10 3c0 2 2 2 3 4" stroke="#f3f3f3" stroke-width="1.3" fill="none"/></svg>
      www.ironspan.com
    </li>
  </ul>
</section>

<section class="card card-back">
  <div class="wordmark">IRONSPAN</div>
  <p class="services">
    Pipelines <span class="dot">•</span>Marine <span class="dot">•</span>Fabrication <span class="dot">•</span>Forestry<br>
    Power <span class="dot">•</span>Ridgeford <span class="dot">•</span>Ashbury <span class="dot">•</span>Port Caldwell<br>
    Elmstone <span class="dot">•</span>Harrowgate
  </p>
</section>

</body>
</html>
```